Brand New Product Needs Sales Focused Website Design

Looking for design of Homepage, Category Page & Product Page for single product sales focused website. TrundleCrate manufacture and distribute a brand new product to the market called PalTote-Case which is a super strong, re-useable, folding & stacking plastic box which can be seen on our current website www.paltote-case.example PalTote-Case was originally developed as an alternative to supermarket carrier bags and was pitched as a box for life against the other low end re-useable products. The original version was made from recycled plastic and pitched very much as environmental product. We are now taking a different direction and have re-designed the boxes in 5 bright and fashionable designs and although we still want the primary focus to be supermarket shopping we want to position the product as a design led, must have shopping and household accessory rather than a boring, cheap looking black plastic box. The new designs will still have the environmental benefits of being able to be re-used thousands of times and being 100% recyclable and save on the imminent 5p tax on carrier bags in the UK however the new designs will not be made from recycled material. Although the main use for PalTote-Case is supermarket shopping it has a multitude of other uses especially where you need temporary storage - laundry, back of the car, moving house/students, gardening, days out, home office filing (will take A4 file), recycling and much more - PalTote-Case is made out of super strong Polypropylene and can be easily washed and sanitised after use and can be folded and unfolded thousands of times and so will last for many years. PalTote-Case is a product that needs to be seen in action to be understood so the web design must quickly and easily communicate what PalTote-Case is and how it works - this can be done with video, images and copy. Our current website does not work for many reasons:- it is too busy, has too much information, tries too hard and ultimately isn't working. Any of the images off our current website can be supplied for use. Once the concept of the website is agreed I can get these photoshopped with the new designs. Pictures of new designs for reference will be attached to this brief. Ultimately we want the website to convert visitors to sales and therefore designers with a proven track record in this field are especially welcome to enter. We also have a Dropbox folder with over 100 product and situation images in - please send email address and we will send an invite to the folder. Due to Christmas period this competition will be run over 15 days however we may choose to extend the deadline to account for the non working days. Any questions feel free to ask - we will respond within 24 hours where possible.

```html
<!DOCTYPE html>
<html lang="en">
<head>
<meta charset="utf-8">
<title>PalTote-Case – Ingenious &amp; Practical</title>
<link href="https://fonts.googleapis.com/css2?family=Open+Sans:wght@400;600;700&family=Pacifico&family=Raleway:wght@400;500&display=swap" rel="stylesheet">
<style>
:root{
  --green-light:#eefbd9;
  --green-mid:#c6f0a0;
  --green-deep:#8dc63f;
  --green-band:#dcf5c0;
  --blue:#3a7fd0;
  --blue-dark:#2a66b5;
  --orange:#f26b1d;
  --grey-bg:#e9e9e9;
  --text:#555;
  --dark:#2f2f2f;
  --darker:#262626;
}
*{margin:0;padding:0;box-sizing:border-box}
html,body{width:860px;height:1200px;overflow:hidden}
body{position:relative;font-family:"Open Sans",sans-serif;color:var(--text);background:#fff}
.abs{position:absolute}
.hero{left:0;top:0;width:860px;height:452px;background:linear-gradient(180deg,var(--green-light) 0%,#d8f6b8 45%,var(--green-mid) 100%)}
.hero-stripe{left:0;top:452px;width:860px;height:6px;background:repeating-linear-gradient(45deg,#e4e4e4 0 2px,#f4f4f4 2px 4px)}
.logo{left:80px;top:0;width:171px;height:80px;background:linear-gradient(#fff,#e9e9e9);box-shadow:0 6px 8px rgba(0,0,0,.18);text-align:center;padding-top:12px}
.logo-name{font-weight:700;font-size:20px;color:var(--green-deep);line-height:1.1}
.logo-tag{font-size:13px;color:#666;margin-top:6px}
.topbar{left:514px;top:0;width:266px;height:27px;background:#b6cc9c;border-radius:0 0 3px 3px;font-size:9.5px;color:#5a6a4a;display:flex;align-items:center}
.topbar .links{padding-left:12px;flex:1}
.topbar .cart{border-left:1px solid #a3b988;height:100%;display:flex;align-items:center;gap:6px;padding:0 6px;font-size:8px;font-weight:700}
.nav{left:285px;top:45px;width:495px;height:36px;background:linear-gradient(#fff,#ececec);box-shadow:0 2px 4px rgba(0,0,0,.12);display:flex;font-size:12px;color:#555}
.nav a{display:flex;align-items:center;justify-content:center;border-right:1px solid #ddd;text-decoration:none;color:inherit}
.nav a.active{background:linear-gradient(#5b9ce0,var(--blue-dark));color:#fff;font-weight:600}
.welcome{left:82px;top:152px;font-family:"Pacifico",cursive;font-size:26px;color:#2d2d2d}
.welcome span{color:var(--green-deep)}
.intro{left:80px;top:202px;width:375px;font-size:10.3px;line-height:16px;color:#666}
.intro p+p{margin-top:16px}
.btn{top:333px;height:35px;border-radius:18px;color:#fff;font-size:12px;font-weight:600;display:flex;align-items:center;justify-content:center;box-shadow:0 0 0 4px rgba(140,190,90,.45)}
.btn-learn{left:84px;width:116px;background:linear-gradient(#ff8a3a,var(--orange))}
.btn-buy{left:215px;width:117px;background:linear-gradient(#6ca8e8,var(--blue-dark))}
.hero-photo{left:505px;top:95px;width:275px;height:357px;background:linear-gradient(160deg,#cfe9b4 0%,#7f9bc9 45%,#3a5bb8 75%,#4a5470 100%)}
.section-title{left:80px;top:474px;font-family:"Raleway",sans-serif;font-weight:400;font-size:17.5px;color:#333}
.rule{left:80px;height:1px;width:700px;background:#ddd}
.video{left:80px;top:516px;width:239px;height:160px;border-radius:3px;background:linear-gradient(135deg,#d8d8d8,#9a9a9a 60%,#6f6f6f)}
.video .time{position:absolute;left:104px;bottom:6px;font-size:9px;color:#fff}
.step{width:80px;text-align:center;font-size:10px;color:#555;line-height:12px}
.step .ring{width:78px;height:78px;border-radius:50%;border:3px solid #9bc447;background:#fff;box-shadow:0 0 0 2px #fff,0 0 0 3px #cfe3a6;margin:0 auto 5px;display:flex;align-items:center;justify-content:center}
.step .ring i{display:block;width:50px;height:34px;background:linear-gradient(#2f5fd8,#1f3fa5);border-radius:3px}
.card{top:721px;width:165px;height:200px;background:var(--grey-bg);text-align:center;padding-top:15px}
.card.featured{background:linear-gradient(#5a9ce0,var(--blue-dark))}
.card .icon{width:58px;height:58px;border-radius:50%;background:#fff;margin:0 auto;display:flex;align-items:center;justify-content:center}
.card h3{font-family:"Raleway",sans-serif;font-weight:500;font-size:14.5px;color:#333;margin-top:14px}
.card p{font-size:10px;line-height:14.5px;color:#999;margin:8px 6px 0}
.card a{display:inline-block;margin-top:9px;font-size:9.5px;color:#333;text-decoration:underline}
.card.featured h3,.card.featured a{color:#fff}
.card.featured p{color:#cfe2f7}
.band{left:0;top:948px;width:860px;height:42px;background:var(--green-band)}
.social{left:79px;top:958px;display:flex;gap:9px}
.social i{display:block;width:23px;height:23px;border-radius:50%;background:#a8b69a}
.subscribe{left:482px;top:953px;display:flex;height:31px}
.subscribe .field{width:210px;background:#b3d493;font-style:italic;font-size:11px;color:#4e5b44;display:flex;align-items:center;padding-left:9px}
.subscribe .go{width:90px;background:#2a2a2a;color:#fff;font-size:11px;display:flex;align-items:center;justify-content:center}
.footer{left:0;top:990px;width:860px;height:169px;background:var(--dark)}
.footer-head{font-family:"Raleway",sans-serif;font-weight:400;font-size:14px;color:#eee}
.site-links{left:79px;top:1010px}
.site-links ul{list-style:none;margin-top:8px;font-size:10.5px;line-height:15.8px;color:#8a8a8a}
.about{left:205px;top:1010px;width:215px}
.about p{margin-top:8px;font-size:10.5px;line-height:15.8px;color:#8a8a8a}
.help{left:469px;top:1030px;width:311px;height:76px;background:#242424;border-radius:3px;padding:14px 14px}
.help h5{font-family:"Raleway",sans-serif;font-weight:400;font-size:20px;color:#fff}
.help .row{display:flex;justify-content:space-between;margin-top:8px;font-family:"Raleway",sans-serif;font-size:10.5px;color:#fff}
.bottom{left:0;top:1159px;width:860px;height:41px;background:var(--darker);font-size:10px;color:#777;display:flex;align-items:center;justify-content:space-between;padding:0 80px 0 79px}
</style>
</head>
<body>
<header>
  <div class="abs hero"></div>
  <div class="abs logo"><div class="logo-name">PalTote-Case</div><div class="logo-tag">Ingenious &amp; Practical</div></div>
  <div class="abs topbar"><span class="links">About Us &nbsp;|&nbsp; Faq &nbsp;|&nbsp; Contact Us</span>
    <span class="cart"><svg width="16" height="13" viewBox="0 0 16 13" fill="none" stroke="#5a6a4a" stroke-width="1.3"><path d="M1 1h3l2 8h8l1-6H5"/><circle cx="7" cy="11.5" r="1"/><circle cx="13" cy="11.5" r="1"/></svg>My Cart items (0)</span></div>
  <nav class="abs nav">
    <a class="active" style="width:67px">Home</a><a style="width:80px">Catagory</a><a style="width:88px">Our Range</a><a style="width:81px">Products</a><a style="width:87px">Gaurantee</a><a style="width:92px;border:0">Contact Us</a>
  </nav>
</header>

<section>
  <div class="abs welcome">Welcome To <span>PalTote-Case</span></div>
  <div class="abs intro">
    <p>The Consumer has already been educated into the ‘Bag For Life’ concept of shopping – PalTote-Case is the perfect answer to those regular customers visiting the store by car and particularly appeals to the ‘heavy’ shopper .</p>
    <p>A rigid stackable box when open, it folds flat into a convenient, compact lightweight ‘briefcase’ for carrying or storage. Using the principles of origami, it folds down and is held together by self-fastenings.</p>
  </div>
  <div class="abs btn btn-learn">LEARN MORE</div>
  <div class="abs btn btn-buy">BUY NOW</div>
  <div class="abs hero-photo" role="img" aria-label="Photo of a shopper holding an open blue folding box full of groceries"></div>
  <div class="abs hero-stripe"></div>
</section>

<section>
  <h2 class="abs section-title">From Featherlight Flat-Pack To Rigid Stacking Box In Seconds!</h2>
  <div class="abs rule" style="top:505px"></div>
  <div class="abs video" role="img" aria-label="Video still demonstrating the folding box">
    <svg class="abs" style="left:95px;top:55px" width="50" height="50" viewBox="0 0 50 50"><circle cx="25" cy="25" r="22" fill="none" stroke="#777" stroke-width="4"/><path d="M19 14l15 11-15 11z" fill="#777"/></svg>
    <span class="time">00:00:03:00</span>
  </div>
  <div class="abs step" style="left:340px;top:553px"><div class="ring" role="img" aria-label="Box folded flat"><i style="height:40px"></i></div>Folded</div>
  <div class="abs step" style="left:430px;top:528px"><div class="ring" role="img" aria-label="Opening the clip"><i style="width:36px;height:40px"></i></div>Open<br>The Clip</div>
  <div class="abs step" style="left:520px;top:526px"><div class="ring" role="img" aria-label="Pulling out the box ends"><i style="width:58px;height:30px"></i></div>Pull<br>Out Ends</div>
  <div class="abs step" style="left:610px;top:537px"><div class="ring" role="img" aria-label="Sliding rails to lock"><i style="width:54px;height:30px"></i></div>Slide Rails<br>To Lock</div>
  <div class="abs step" style="left:701px;top:553px"><div class="ring" role="img" aria-label="Stacked box"><i style="width:44px;height:42px"></i></div>Stack Too!</div>
  <div class="abs rule" style="top:699px;background:#eee"></div>
</section>

<section>
  <div class="abs card featured" style="left:86px"><div class="icon"><svg width="32" height="26" viewBox="0 0 32 26"><ellipse cx="13" cy="11" rx="12" ry="9" fill="#f3b51c"/><ellipse cx="19" cy="13" rx="12" ry="9" fill="#ffd43a"/><path d="M22 20l4 5-9-4z" fill="#ffd43a"/></svg></div><h3>What Do You Think?</h3><p>We Really Do Want To Hear Your Opinions And Comments. Let Us Know What You Think &amp; Read Our Reviews</p><a>LEARN MORE</a></div>
  <div class="abs card" style="left:261px"><div class="icon"><svg width="28" height="28" viewBox="0 0 28 28"><rect x="4" y="4" width="20" height="20" rx="3" fill="#2e3640"/><rect x="10" y="10" width="14" height="8" fill="#fff"/></svg></div><h3>Plastic Polution</h3><p>We Really Do Want To Hear Your Opinions And Comments. Let Us Know What You Think &amp; Read Our Reviews</p><a>LEARN MORE</a></div>
  <div class="abs card" style="left:435px"><div class="icon"><svg width="32" height="28" viewBox="0 0 32 28"><path d="M4 10h24v16H4z" fill="#b57a3c"/><path d="M4 10l4-6h16l4 6z" fill="#d69a55"/></svg></div><h3>PalTote-Case Videos</h3><p>We Really Do Want To Hear Your Opinions And Comments. Let Us Know What You Think &amp; Read Our Reviews</p><a>LEARN MORE</a></div>
  <div class="abs card" style="left:610px"><div class="icon"><svg width="36" height="36" viewBox="0 0 36 36"><circle cx="18" cy="18" r="17" fill="#d8232a"/><circle cx="18" cy="18" r="11" fill="none" stroke="#fff" stroke-width="1.5"/></svg></div><h3>Life Time Guarantee</h3><p>We Really Do Want To Hear Your Opinions And Comments. Let Us Know What You Think &amp; Read Our Reviews</p><a>LEARN MORE</a></div>
</section>

<footer>
  <div class="abs band"></div>
  <div class="abs social"><i></i><i></i><i></i><i></i><i></i></div>
  <div class="abs subscribe"><div class="field">Enter your email address</div><div class="go">Subscribe Here</div></div>
  <div class="abs footer"></div>
  <div class="abs site-links"><div class="footer-head">Site Links</div><ul><li>Home</li><li>Catagory</li><li>Our Range</li><li>Products</li><li>Guarantee</li><li>Contact Us</li></ul></div>
  <div class="abs about"><div class="footer-head">About Us</div><p>Lorem ipsum dolor sit amet, consectetur adipiscing elit, sed do eiusmod tempor incididunt ut labore et dolore magna aliqua. Ut enim ad minim veniam, quis nostrud exercitation ullamco laboris nisi ut aliquip ex ea commodo consequat.</p></div>
  <div class="abs help"><h5>Need Help?</h5><div class="row"><span>Email: info@paltote-case.example</span><span>0800-555-0199-2</span></div></div>
  <div class="abs bottom"><span>Copyright © paltote-case.example - All Rights Reserved</span><span>Privacy Policy &nbsp; | &nbsp; Terms Of Uses</span></div>
</footer>
</body>
</html>
```